Business card design for new eCommerce site focusing on integrity and strong businsess tactics

We need a business card that will stand out and be memorable. Something with color that matches our company logo colors. Think high end version of Pactivo. There are 2 logos provided. The parent company is called Amber Ledge Partners and we are presenting a new and very exciting eCommerce site called BrightHarborTrade.example.

Target Market(s)

Our target markets are in the Activities, Food and Beverage, Health and Beauty

Industry/Entity Type

Marketing

Contact Information for Business Card

We have 4 members that need cards...I will provide all info to the winner of the design contest
Business Address is
4870 West 63rd Avenue, Suite C207
Phoenix AZ 85731

Font styles to use
Serif
Sans Serif

Colors

Designer to choose colors to be used in the design.

Requirements
Must have
• The card must be memorable...should be unique in design but must exude integrity and be playful .
• I have provided several colors or our parent company...please feel free to use which ever
Nice to have
• I will leave this up to you. Feel free to use other images of your choosing that wraps around our client.....Activities, Dining, Health, Beauty
Should not have
• just dont be boring

```html
<!DOCTYPE html>
<html lang="en">
<head>
<meta charset="utf-8">
<title>BrightHarborTrade.example business card</title>
<link rel="stylesheet" href="https://fonts.googleapis.com/css2?family=Questrial&display=swap">
<style>
  :root {
    --backdrop: #2b2b2b;
    --paper: #f3f3f3;
    --brand-blue: #2e7bb0;
    --brand-green: #76b82a;
    --ink-grey: #5a5a5a;
    --white: #ffffff;
  }
  * { margin: 0; padding: 0; box-sizing: border-box; }
  html, body {
    width: 1200px; height: 960px; overflow: hidden;
    background: var(--backdrop);
    font-family: "Questrial", "Century Gothic", sans-serif;
  }
  .card {
    position: absolute;
    width: 600px; height: 343px; overflow: hidden;
  }
  .card--front { left: 314px; top: 113px; background: var(--paper); }
  .card--back { left: 311px; top: 472px; background: var(--brand-green); }

  .card__waves { position: absolute; inset: 0; }

  .brand {
    position: absolute; left: 42px; top: 62px;
    display: flex; flex-direction: column; gap: 4px;
  }
  .brand__row { display: flex; align-items: center; gap: 8px; }
  .brand__dot {
    width: 16px; height: 16px; border-radius: 50%;
    background: var(--brand-blue);
  }
  .brand__name { color: var(--brand-green); font-size: 20px; }
  .brand__tagline {
    color: var(--ink-grey); font-size: 11px; letter-spacing: 0.6px;
    padding-left: 24px;
  }

  .contact {
    position: absolute; right: 36px; top: 132px;
    text-align: right; color: var(--white);
  }
  .contact__name { color: var(--brand-green); font-size: 21px; letter-spacing: 0.5px; }
  .contact__role { font-size: 15px; margin-top: 2px; }
  .contact__address { font-size: 14.5px; line-height: 18px; margin-top: 14px; }
  .contact__lines { list-style: none; margin-top: 11px; font-size: 14.5px; line-height: 19px; }
  .contact__lines li { display: flex; justify-content: flex-end; align-items: center; gap: 7px; }
  .contact__icon { width: 12px; height: 12px; flex: none; }

  .parent {
    position: absolute; inset: 0;
    display: flex; flex-direction: column; align-items: center;
    padding-top: 70px; gap: 18px;
  }
  .parent__ring {
    width: 146px; height: 146px; border-radius: 50%;
    border: 3px solid var(--white);
  }
  .parent__name { color: var(--white); font-size: 34px; }
</style>
</head>
<body>
  <section class="card card--front">
    <svg class="card__waves" width="600" height="343" viewBox="0 0 600 343" aria-hidden="true">
      <path d="M376 0 C405 60 262 168 244 232 C232 276 262 318 284 343 L600 343 L600 0 Z" fill="var(--brand-green)"/>
      <path d="M385 0 C418 62 282 170 258 232 C244 272 272 318 293 343 L600 343 L600 0 Z" fill="var(--brand-blue)"/>
      <path d="M396 0 C432 64 300 172 274 234 C260 272 288 318 308 343" fill="none" stroke="var(--white)" stroke-width="2.5"/>
    </svg>

    <div class="brand">
      <div class="brand__row">
        <span class="brand__dot"></span>
        <span class="brand__name">BrightHarborTrade.example</span>
      </div>
      <span class="brand__tagline">Trusted-Trade-Smart-Living</span>
    </div>

    <div class="contact">
      <p class="contact__name">DANIEL REYES</p>
      <p class="contact__role">CEO/FOUNDER</p>
      <p class="contact__address">4870 West 63rd Avenue<br>Suite C207, Phoenix AZ 85731</p>
      <ul class="contact__lines">
        <li>602 555 0148
          <svg class="contact__icon" viewBox="0 0 12 12"><path d="M2.5 1 L4.5 1 L5 3.5 L3.8 4.5 C4.5 6 6 7.5 7.5 8.2 L8.5 7 L11 7.5 L11 9.5 C11 10.5 10 11 9 11 C4.5 10.5 1.5 7.5 1 3 C1 2 1.5 1 2.5 1 Z" fill="var(--brand-green)"/></svg>
        </li>
        <li>602 555 0193
          <svg class="contact__icon" viewBox="0 0 12 12"><rect x="3" y="0.8" width="6" height="10.4" rx="1" fill="none" stroke="var(--brand-green)" stroke-width="1.3"/><circle cx="6" cy="9.4" r="0.7" fill="var(--brand-green)"/></svg>
        </li>
        <li>daniel@brightharbortrade.example
          <svg class="contact__icon" viewBox="0 0 12 12"><rect x="0.5" y="2.5" width="11" height="7.5" fill="var(--brand-green)"/><path d="M0.8 2.8 L6 7 L11.2 2.8" fill="none" stroke="var(--brand-blue)" stroke-width="1"/></svg>
        </li>
        <li>www.brightharbortrade.example
          <svg class="contact__icon" viewBox="0 0 12 12"><circle cx="6" cy="6" r="5.5" fill="var(--brand-green)"/><path d="M0.5 6 H11.5 M6 0.5 C3 3.5 3 8.5 6 11.5 M6 0.5 C9 3.5 9 8.5 6 11.5" fill="none" stroke="var(--brand-blue)" stroke-width="0.8"/></svg>
        </li>
      </ul>
    </div>
  </section>

  <section class="card card--back">
    <div class="parent">
      <span class="parent__ring"></span>
      <p class="parent__name">Amber Ledge Partners</p>
    </div>
  </section>
</body>
</html>
```